Contemporary Business card for Event Manager

Needed for my startup events company in Melbourne. Events I manage will be based within the fashion industry, sporting events, product launches etc. Not weddings or small dinner parties. Therfore I am after something professional and aimed at high end corporate market; but with the added emphasis on not being too conservative or boring. I am happy with a pop of colour e.g. yellow or copper foil.

Target Market(s)

fashion industry, design industry, high end sporting events e.g. Polo, Grand Prix, corporate clients,

Industry/Entity Type

Fashion

Contact Information for Business Card

side 1
Lucy Brandt (can be upper or lower case, have a feature full stop between first and surname, or at the end of the nameetc) I am open to ideas. I would also be fine with my initials or name as a logo on the front (if this is the case my full name would need to go on the second side of the card.
2nd side:
Mobile: +61 400 817 263
email: lucy.brandt@mailnest.com.au

on one side of the card:
event management | brand activation | Advisory Services

Font styles to use
Serif
Sans Serif

Requirements
Must have
• side 2 must have
• mobile number
• email address
• event management | brand activation | Advisory Services
• ** my full name (Lucy Brandt) must be on the card somewhere)
Nice to have
• 1st side
• I see the card stock being either a dark grey, light grey, natural white or black (all matt colours on unprocessed card). I see the writing being copper foil, or foil white or foil black.
• To give you a feel for me, think: contemporary, minimalist, I love line drawings, concrete, white with grey vein marble, copper, white, grey, black...yes I do like colour....yellow (but pops of colour) ;) I would like the card to look designer but 'on trend' as I deal with a lot of design and fashion clients....styles - think the sophistication and simplicity of Vireaux or urban contemporary.
• some examples of what I like. Although please don't leet this limit you...I really am happy to have something a little more urban or design focused like a line drawing of an object, person too or a photo image too.
• https://www.moodtackle.com/pin/830165427719302846/
• https://www.moodtackle.com/pin/607281935540173268/
• https://www.moodtackle.com/pin/318746205913457092/
• https://www.moodtackle.com/pin/41983627530918476/
• https://www.moodtackle.com/pin/53128940672419087/
• https://www.moodtackle.com/pin/90316284750638152/
• https://www.moodtackle.com/pin/734092618450362918/
• https://www.moodtackle.com/pin/926354081736215407/
• https://www.moodtackle.com/pin/481627093518704356/
Should not have
• should not look commercial or have cartoonish looking logos. However happy with a simple line drawing or logo with initials etc.

```html
<!DOCTYPE html>
<html lang="en">
<head>
<meta charset="utf-8">
<title>Lucy Brandt — Business Card</title>
<link href="https://fonts.googleapis.com/css2?family=Montserrat:wght@500;600&family=Open+Sans:wght@600&display=swap" rel="stylesheet">
<style>
  :root {
    --backdrop: #3a332f;
    --card-stock: #111111;
    --card-stock-edge: #1b1b1b;
    --silver-light: #e9e9e9;
    --silver-mid: #9c9c9c;
    --silver-dark: #5e5e5e;
    --gold-light: #ffe37a;
    --gold-mid: #f2c500;
    --gold-dark: #c99a0a;
  }
  * { box-sizing: border-box; margin: 0; padding: 0; }
  html, body {
    width: 1200px;
    height: 780px;
    overflow: hidden;
    background: var(--backdrop);
  }
  .card-set {
    position: absolute;
    inset: 0;
    display: flex;
    align-items: center;
    justify-content: center;
    gap: 44px;
  }
  .card {
    position: relative;
    width: 520px;
    height: 300px;
    background: var(--card-stock);
    border: 1px solid var(--card-stock-edge);
    border-radius: 3px;
    box-shadow: 0 14px 30px rgba(0,0,0,0.45);
  }
  .card-front .holder-name {
    position: absolute;
    left: 52px;
    top: 112px;
    font-family: "Open Sans", Arial, sans-serif;
    font-weight: 600;
    font-size: 56px;
    letter-spacing: 0.5px;
    line-height: 1;
    background: linear-gradient(100deg, var(--silver-dark) 0%, var(--silver-mid) 25%, var(--silver-light) 55%, var(--silver-mid) 80%, var(--silver-light) 100%);
    -webkit-background-clip: text;
    background-clip: text;
    color: transparent;
  }
  .card-back .contact-block {
    position: absolute;
    right: 30px;
    top: 118px;
    text-align: right;
    font-family: "Montserrat", Arial, sans-serif;
    background: linear-gradient(100deg, var(--gold-dark) 0%, var(--gold-mid) 40%, var(--gold-light) 70%, var(--gold-mid) 100%);
    -webkit-background-clip: text;
    background-clip: text;
    color: transparent;
  }
  .contact-phone {
    font-weight: 600;
    font-size: 38px;
    line-height: 1.05;
    letter-spacing: 0.5px;
  }
  .contact-email {
    font-weight: 500;
    font-size: 20px;
    line-height: 1.3;
    letter-spacing: 0.3px;
  }
  .service-list {
    margin-top: 8px;
    font-weight: 500;
    font-size: 15px;
    letter-spacing: 0.3px;
    white-space: nowrap;
  }
</style>
</head>
<body>
  <main class="card-set">
    <section class="card card-front" aria-label="Card front">
      <h1 class="holder-name">Lucy Brandt.</h1>
    </section>
    <section class="card card-back" aria-label="Card back">
      <div class="contact-block">
        <p class="contact-phone">+61 400 817 263</p>
        <p class="contact-email">lucy.brandt@mailnest.com.au</p>
        <p class="service-list">event management | brand activation | Advisory Services</p>
      </div>
    </section>
  </main>
</body>
</html>
```